New Wordpress Design Project

The website is my name tessamaywarden.com

I need a website design that will be graphically pleasing and have a crisp feel to it. I am a business and personal coach and have many different niches that I work with. I am looking for the central site to describe who I am and how I help people - I help people "wake up" to make conscious choices in their lives. I use hypnosis but do not want it to be esoteric, I ground the hypnosis and base it in science of how people can manage their state to reach their full potential in their lives and in business. I work one on one but also do public speaking and recently started to do trainings with corporations, helping people improve their business. I am looking at this as a merge of hypnosis and other tools with the business or corporate world - based in science - neuroplasticity, brain training etc. I will be helping people to overcome anxiety and stress, limiting beliefs, controlling and choosing habits that will work for them, fears and phobias, golf/sports improvement, weight loss.

Really helping people to center back with themselves, to not be so caught up in their head but drop into their heart and with what is really going on. My mission is to connect them back with themselves, using language, state and conscious choice.

I work online with entrepreneurs helping them to get unstuck, move past fears and limiting beliefs to create the business of their dreams.

I added a file of what I am envisioning on the right hand side of my site to show people the different niches I am involved with.

Some sites that I like www.janetbrookwell.com www.corinnedalby.org http://www.pamkestrel.com/ , Details for my new Wordpress Design Project will be added soon. , The website is my name tessamaywarden.com

the square boxes graphic below is similar to one that I will be making for a page on my site for clarity and crispness. But will be creating it more in the teal color.

Target Market(s)

My target market are both male and female 30-50 either entreprenuers/business people

Industry/Entity Type

Training

Requirements
Must have
• A video with an opt in box
My background color is teal/blue (see below file)
Social media links

```html
<!DOCTYPE html>
<html lang="en">
<head>
<meta charset="utf-8">
<title>Tessa May Warden – Optimizing Your Mindset for Entrepreneurial Success</title>
<link rel="stylesheet" href="https://fonts.googleapis.com/css2?family=Ubuntu:wght@300;400;500;700&display=swap">
<style>
:root{
  --teal:#14b39b;
  --teal-dark:#0e9a85;
  --teal-deep:#0a6f62;
  --pink:#e2478f;
  --pink-light:#f56ea9;
  --pink-dark:#b52a6a;
  --yellow:#f3e327;
  --ink:#555;
  --ink-soft:#777;
  --line:#dedede;
  --footer:#383838;
  --white:#fff;
}
*{margin:0;padding:0;box-sizing:border-box}
html,body{width:722px;height:1200px;overflow:hidden}
body{position:relative;background:var(--white);font-family:"Ubuntu",sans-serif;color:var(--ink)}

/* header */
.site-header{position:absolute;left:0;top:0;width:722px;height:70px;background:var(--teal)}
.brand{position:absolute;left:56px;top:14px}
.brand-name{display:flex;align-items:center;gap:6px;font-size:21px;font-weight:500;color:var(--yellow);letter-spacing:-.2px}
.brand-dot{width:14px;height:14px;border-radius:50%;background:var(--yellow)}
.brand-tagline{margin:3px 0 0 42px;font-size:7px;color:var(--white);font-weight:300}
.main-nav{position:absolute;right:48px;top:34px;display:flex;font-size:10px;font-weight:500}
.main-nav a{color:var(--white);text-decoration:none;padding:0 10px;border-left:1px solid rgba(255,255,255,.35)}
.main-nav a:first-child{border-left:0}

/* hero */
.hero-band{position:absolute;left:0;top:70px;width:722px;height:283px;background:linear-gradient(#fff,#f2f2f2);border-bottom:1px solid #e6e6e6}
.hero{position:absolute;left:51px;top:82px;width:620px;height:251px;overflow:hidden;box-shadow:0 1px 4px rgba(0,0,0,.35)}
.hero-photo{position:absolute;inset:0;background:radial-gradient(ellipse at 48% 45%,#5ad6b0 0%,#2a9a7c 35%,#14584a 70%,#0d3a32 100%)}
.hero-title{position:absolute;left:0;right:0;top:84px;text-align:center;color:var(--white);font-size:40px;font-weight:700;letter-spacing:5px;line-height:1}
.hero-sub{position:absolute;left:0;right:0;top:127px;text-align:center;color:var(--white);font-size:17px;font-weight:500;letter-spacing:6px}
.hero-dots{position:absolute;left:0;right:0;bottom:7px;display:flex;justify-content:center;gap:3px}
.hero-dots span{width:8px;height:8px;border-radius:50%;background:var(--teal)}
.hero-dots span.is-active{background:var(--white)}

/* posts */
.post{position:absolute;left:54px;width:420px;height:120px}
.post-title{position:absolute;left:0;top:0;font-size:17px;font-weight:400;color:var(--pink);white-space:nowrap}
.post-thumb{position:absolute;left:2px;top:17px;width:128px;height:92px}
.post-excerpt{position:absolute;left:139px;top:17px;width:278px;font-size:7.6px;line-height:13.3px;color:var(--ink-soft)}
.post-meta{position:absolute;left:139px;top:76px;font-size:7px;color:var(--ink)}
.read-more{position:absolute;left:139px;top:88px;width:70px;height:20px;border-radius:3px;background:var(--teal);color:var(--white);font-size:7.5px;font-weight:500;text-align:center;line-height:20px;text-decoration:none}
.post-divider{position:absolute;left:54px;width:420px;height:1px;background:var(--line)}

.pager{position:absolute;left:57px;top:1093px;display:flex;gap:5px}
.pager span{width:16px;height:15px;border:1px solid #ccc;font-size:8px;line-height:13px;text-align:center;color:#666;background:#fafafa}
.pager span.is-current{background:var(--pink);border-color:var(--pink);color:var(--white)}

/* sidebar */
.widget-box{position:absolute;left:504px;width:168px;border:1px solid #ddd;background:var(--white)}
.widget-head{position:absolute;left:495px;width:178px;height:29px;color:var(--white);font-size:12.5px;padding:7px 0 0 21px}
.widget-head.pink{background:linear-gradient(var(--pink-light),var(--pink))}
.widget-head.teal{background:var(--teal)}
.widget-head::after{content:"";position:absolute;left:0;top:29px;border-top:9px solid var(--pink-dark);border-left:9px solid transparent}
.widget-head.teal::after{border-top-color:var(--teal-deep)}

.video-box{position:absolute;left:495px;top:374px;width:177px;height:123px;border:1px solid #ddd;padding:3px;background:var(--white)}
.video-frame{position:relative;width:100%;height:100%;background:linear-gradient(100deg,#3a2e24 0%,#6b5a48 45%,#b6a796 100%)}
.play-btn{position:absolute;left:72px;top:45px}

.avatar{position:absolute;background:linear-gradient(#e9d3a8,#d9b488 60%,#c9d6e6)}
.meet-text{position:absolute;font-size:7.4px;line-height:13.3px;color:var(--ink)}
.recent-list{position:absolute;left:521px;top:690px;list-style:none;font-size:7.4px;color:var(--ink)}
.recent-list li{position:relative;padding-left:7px;margin-bottom:7px;width:140px;line-height:10px}
.recent-list li::before{content:"";position:absolute;left:0;top:2px;border-left:3px solid #666;border-top:3px solid transparent;border-bottom:3px solid transparent}
.fan-name{position:absolute;left:561px;top:848px;font-size:8.5px;color:#333}
.like-btn{position:absolute;left:561px;top:862px;width:31px;height:12px;border:1px solid #c3cbd8;background:#eef1f6;border-radius:2px;font-size:6.5px;line-height:10px;color:#4a5a80;padding-left:13px}
.like-btn::before{content:"";position:absolute;left:3px;top:2px;width:6px;height:6px;background:#8a98b8;border-radius:1px}
.fan-count{position:absolute;left:561px;top:879px;font-size:7px;color:#333}
.fan-post{position:absolute;left:560px;top:897px;width:108px;font-size:7px;line-height:12.3px;color:var(--ink-soft)}

/* footer */
.site-footer{position:absolute;left:0;top:1130px;width:722px;height:70px;background:var(--footer)}
.footer-nav{position:absolute;left:54px;top:21px;font-size:9px;color:var(--white);font-weight:500}
.footer-nav span{padding:0 5px;color:#bbb}
.copyright{position:absolute;left:54px;top:39px;font-size:7px;color:#bbb}
.social{position:absolute;left:586px;top:18px;display:flex;gap:3px}
.social a{width:18px;height:18px;border-radius:50%;background:var(--white)}
</style>
</head>
<body>

<header class="site-header">
  <div class="brand">
    <div class="brand-name"><span class="brand-dot"></span>TessaMayWarden.com</div>
    <div class="brand-tagline">Optimizing Your Mindset for Entrepreneurial Success</div>
  </div>
  <nav class="main-nav">
    <a href="#">HOME</a><a href="#">MY STORY</a><a href="#">COACHING</a><a href="#">TESTIMONIALS</a><a href="#">CONTACT</a>
  </nav>
</header>

<div class="hero-band"></div>
<section class="hero">
  <div class="hero-photo" role="img" aria-label="Teal-tinted portrait of the coach among leaves"></div>
  <h1 class="hero-title">DUIS TINCIDUNT</h1>
  <div class="hero-sub">SUSPENDDISSE VULPUTATE</div>
  <div class="hero-dots"><span class="is-active"></span><span></span><span></span><span></span></div>
</section>

<main>
  <article class="post" style="top:376px">
    <h2 class="post-title">Are you sleepwalking through life?</h2>
    <div class="post-thumb" role="img" aria-label="Person walking through a dry rocky landscape" style="background:linear-gradient(#8a8a5c,#b89b6c 55%,#9c7a50)"></div>
    <p class="post-excerpt">Do you keep hearing everyone talking about authenticity, knowing who you are and not really worrying about what other's think about it? I know I do! &nbsp;It seems everywhere I turn, newspapers, magazines I keep hearing this message. ...</p>
    <div class="post-meta">Written by TESSA MAY on December 7, 2012 · Leave a Comment</div>
    <a class="read-more" href="#">READ MORE</a>
  </article>
  <div class="post-divider" style="top:508px"></div>

  <article class="post" style="top:521px">
    <h2 class="post-title">Set Your Goals on Fire!</h2>
    <div class="post-thumb" role="img" aria-label="Pencil crossing out a word on paper" style="background:linear-gradient(120deg,#c9a070,#dfe6f2 45%,#b8c8e6)"></div>
    <p class="post-excerpt">I'm sure everyone reading this has set a goal, whether it was New Year's Eve goals, fitness or monetary goals and come up far short of meeting them. In fact I am pretty sure most of the goals people set never come to fruition. I know I certainly...</p>
    <div class="post-meta">Written by TESSA MAY on December 7, 2012 · Leave a Comment</div>
    <a class="read-more" href="#">READ MORE</a>
  </article>
  <div class="post-divider" style="top:653px"></div>

  <article class="post" style="top:666px">
    <h2 class="post-title">Neuroplasticity. What is it and what can it do for you?</h2>
    <div class="post-thumb" role="img" aria-label="Glowing network of neurons" style="background:radial-gradient(circle at 40% 45%,#d0703a,#6a2a1e 50%,#2a1412)"></div>
    <p class="post-excerpt">What fires together, wires together." This is a paraphrase coined by a psychologist Daniel Hollis, it has become the catch phrase to describe how neural networks are formed in our brain. Every time you experience something you create new</p>
    <div class="post-meta">Written by TESSA MAY on December 7, 2012 · Leave a Comment</div>
    <a class="read-more" href="#">READ MORE</a>
  </article>
  <div class="post-divider" style="top:799px"></div>

  <article class="post" style="top:811px">
    <h2 class="post-title">Emotional Resilience is Good For You</h2>
    <div class="post-thumb" role="img" aria-label="Joyful woman with raised arms in a yellow flower field" style="background:linear-gradient(#b8d8f0,#e0ecf4 40%,#e8d640 60%,#c9b820)"></div>
    <p class="post-excerpt">Every time you provoke a positive emotion, you increase your creativity, stamina and will power. Curiosity and love are just two of the emotions you can learn to provoke anytime, anywhere. Doing just five things that make you feel better per day is...</p>
    <div class="post-meta">Written by TESSA MAY on December 7, 2012 · Leave a Comment</div>
    <a class="read-more" href="#">READ MORE</a>
  </article>
  <div class="post-divider" style="top:944px"></div>

  <article class="post" style="top:956px">
    <h2 class="post-title">Can you really rewire your brain for success?</h2>
    <div class="post-thumb" role="img" aria-label="Silhouette with raised arms against a sunset sky" style="background:linear-gradient(#3a4a8a,#b87a6a 55%,#e0a050 75%,#2a2020)"></div>
    <p class="post-excerpt">Yes, you can rewire your brain! &nbsp;Using the latest scientific and neurological research to retrain your brain. In the past decade, scientists have discovered that the brain is not a rigid organ like it was once believed. It can be molded based on...</p>
    <div class="post-meta">Written by TESSA MAY on December 7, 2012 · Leave a Comment</div>
    <a class="read-more" href="#">READ MORE</a>
  </article>

  <nav class="pager"><span>«</span><span class="is-current">1</span><span>2</span><span>3</span><span>4</span><span>5</span><span>6</span><span>»</span></nav>
</main>

<aside>
  <div class="video-box">
    <div class="video-frame" role="img" aria-label="Welcome video of the coach speaking">
      <svg class="play-btn" width="28" height="28" viewBox="0 0 28 28"><circle cx="14" cy="14" r="12.5" fill="rgba(0,0,0,.45)" stroke="#fff" stroke-width="2"/><path d="M11 8.5v11l9-5.5z" fill="#fff"/></svg>
    </div>
  </div>

  <div class="widget-box" style="top:520px;height:121px"></div>
  <div class="widget-head pink" style="top:503px">Meet Tessa May</div>
  <div class="avatar" role="img" aria-label="Portrait of the coach" style="left:516px;top:541px;width:42px;height:38px"></div>
  <p class="meet-text" style="left:562px;top:540px;width:106px">I am an entrepreneur and coach, I help you get your Inner-Game working so you</p>
  <p class="meet-text" style="left:514px;top:581px;width:156px">have Outer-Game success! I have an obses-sion with the mechanics of our thoughts and actions and the neuroscience behind it.</p>

  <div class="widget-box" style="top:666px;height:134px"></div>
  <div class="widget-head pink" style="top:648px">Recent Blog Post</div>
  <ul class="recent-list">
    <li>What is stopping you?</li>
    <li>Are you sleepwalking through life?</li>
    <li>Set Your Goals on Fire!</li>
    <li>Emotional Resilience is Good For You</li>
    <li>Neuroplasticity. What is it and what can it do for you?</li>
  </ul>

  <div class="widget-box" style="top:828px;height:176px"></div>
  <div class="widget-head teal" style="top:810px">Join the Community</div>
  <div class="avatar" role="img" aria-label="Profile photo of the coach" style="left:516px;top:849px;width:36px;height:36px"></div>
  <div class="fan-name">Tessa May Warden</div>
  <div class="like-btn">Like</div>
  <div class="fan-count">481 people like</div>
  <div class="avatar" role="img" aria-label="Profile photo of the coach" style="left:516px;top:900px;width:36px;height:36px"></div>
  <p class="fan-post">As 2013 comes to a close my wish for you is for a blessed 2014, filled with clarity, passion and abundance. Decide what you want to create this year as the clock strikes 12 see it clearly and your dream will be your reality.</p>
</aside>

<footer class="site-footer">
  <div class="footer-nav">HOME<span>|</span>MY STORY<span>|</span>COACHING<span>|</span>TESTIMONIALS<span>|</span>CONTACT</div>
  <div class="copyright">© 2014 Company Name. &nbsp;All right reserved.</div>
  <div class="social"><a href="#" aria-label="Social link"></a><a href="#" aria-label="Social link"></a><a href="#" aria-label="Social link"></a><a href="#" aria-label="Social link"></a></div>
</footer>

</body>
</html>
```